Business Card Design

Electronic Security
Alarm Systems
CCTV
Electronic Access Control
Security System Integration

Industry/Entity Type

Business

Contact Information for Business Card

Gareth Linwood
PO Box 862
Ashgrove Qld 4071
Phone 07 38526147
Mob 0427395816

```html
<!DOCTYPE html>
<html lang="en">
<head>
<meta charset="utf-8">
<title>Business Card – Gareth Linwood</title>
<link href="https://fonts.googleapis.com/css2?family=Montserrat:wght@600&family=Questrial&display=swap" rel="stylesheet">
<style>
  :root {
    --page-bg: #d9d6d1;
    --card-white: #ffffff;
    --card-black: #111111;
    --text-light: #ffffff;
    --text-dark: #1a1a1a;
    --accent-orange: #f29a1f;
    --accent-blue: #2a9fd6;
    --rule-gold: #b7832c;
  }
  * { box-sizing: border-box; margin: 0; padding: 0; }
  html, body {
    width: 1200px; height: 800px; overflow: hidden;
    background: var(--page-bg);
  }
  .canvas {
    width: 1200px; height: 800px;
    display: flex; align-items: center; justify-content: center;
  }
  .card {
    position: relative;
    width: 990px; height: 600px;
    background: var(--card-white);
    box-shadow: 0 10px 30px rgba(0,0,0,.25);
    overflow: hidden;
    font-family: "Questrial", sans-serif;
  }
  .card__divider {
    position: absolute; left: 0; right: 0; top: 262px;
    height: 3px; background: var(--card-black);
  }
  .card__band {
    position: absolute; left: 0; right: 0; top: 272px; bottom: 0;
    background: var(--card-black);
  }
  .brand {
    position: absolute; right: 150px; top: 150px;
    display: flex; align-items: center; gap: 16px;
  }
  .brand__mark {
    width: 22px; height: 22px; background: var(--accent-blue);
  }
  .brand__name {
    font-size: 52px; letter-spacing: 2px; color: var(--text-dark);
    line-height: 1;
  }
  .brand__tagline {
    border-left: 2px solid var(--text-dark);
    padding-left: 10px;
    font-size: 12px; line-height: 1.15; color: var(--text-dark);
    width: 80px;
  }
  .contact {
    position: absolute; left: 70px; top: 322px;
    width: 380px; text-align: right;
    color: var(--text-light);
  }
  .contact__name {
    font-family: "Montserrat", sans-serif; font-weight: 600;
    font-size: 30px; letter-spacing: 1px;
  }
  .contact__phones {
    margin-top: 18px;
    font-size: 24px; line-height: 1.45; letter-spacing: 1px;
  }
  .contact__address {
    margin-top: 4px; font-size: 24px; letter-spacing: 1px; line-height: 1.45;
  }
  .icons {
    position: absolute; left: 468px; top: 388px;
    display: flex; flex-direction: column; gap: 12px;
  }
  .icons svg { width: 24px; height: 24px; display: block; }
  .vrule {
    position: absolute; left: 520px; top: 330px;
    width: 2px; height: 190px;
    background: linear-gradient(to bottom, transparent, var(--rule-gold) 30%, var(--accent-orange) 70%, transparent);
  }
  .services {
    position: absolute; left: 560px; top: 350px;
    list-style: none; color: var(--text-light);
    font-size: 26px; line-height: 1.3; letter-spacing: 1px;
  }
</style>
</head>
<body>
<main class="canvas">
  <article class="card">
    <div class="card__divider"></div>
    <div class="card__band"></div>

    <div class="brand">
      <span class="brand__mark"></span>
      <span class="brand__name">TREVASK</span>
      <span class="brand__tagline">Trevask Electronic Security Systems</span>
    </div>

    <section class="contact">
      <h1 class="contact__name">Gareth Linwood</h1>
      <p class="contact__phones">0427395816<br>07 38526147</p>
      <p class="contact__address">PO Box 862 Ashgrove Qld 4071</p>
    </section>

    <div class="icons" aria-hidden="true">
      <svg viewBox="0 0 24 24"><rect x="3" y="5" width="18" height="14" rx="2" fill="none" stroke="var(--accent-orange)" stroke-width="2.2"/></svg>
      <svg viewBox="0 0 24 24"><path d="M7 3 L10 7 L8 9 C9 12 12 15 15 16 L17 14 L21 17 L19 21 C11 20 4 13 3 5 Z" fill="var(--accent-orange)"/></svg>
      <svg viewBox="0 0 24 24"><path d="M12 2 C7 2 4 6 4 10 C4 15 12 22 12 22 C12 22 20 15 20 10 C20 6 17 2 12 2 Z" fill="none" stroke="var(--accent-orange)" stroke-width="2.2"/></svg>
    </div>

    <div class="vrule"></div>

    <ul class="services">
      <li>Electronic Security</li>
      <li>Alarm Systems</li>
      <li>CCTV</li>
      <li>Electronic Access Control</li>
      <li>Security System Integration</li>
    </ul>
  </article>
</main>
</body>
</html>
```